Book cover for book about Climate Change

Looking for a clean, bold, and attractive cover for a mass-market paperback (5.5"x 8.5") about solving the climate change problem. Title is either "Where the Rivers Meet” or A Harbor Made of Glass” (your choice), subtitle is "A practical field guide to mending the weather — so that the young ones after us inherit steady seasons and open skies," author is Lorne Whitcombe. Thinking that it *might* feature an image of Earth (or a portion thereof) and its very thin layer of atmosphere -- but STRONGLY encourage other ideas too!

Requirements
Nice to have
• Keep it positive — NOT scary doom-and-gloom

```html
<!DOCTYPE html>
<html lang="en">
<head>
<meta charset="utf-8">
<title>Where the Rivers Meet — Book Cover</title>
<link href="https://fonts.googleapis.com/css2?family=Teko:wght@500&family=Allura&family=Arimo:wght@400;700&display=swap" rel="stylesheet">
<style>
  :root {
    --page: #ffffff;
    --night: #0b1a4a;
    --deep: #1a2d86;
    --blue: #2446b8;
    --haze: #5a86e0;
    --glow: #bcd6ff;
    --ink-light: #fbf8fb;
    --accent: #f2c7a6;
  }
  html, body {
    margin: 0;
    width: 1200px;
    height: 1200px;
    overflow: hidden;
    background: var(--page);
  }
  .cover {
    position: absolute;
    left: 244px;
    top: 39px;
    width: 731px;
    height: 1128px;
    overflow: hidden;
    background: linear-gradient(180deg, var(--night) 0%, #132670 35%, var(--deep) 60%, var(--blue) 100%);
  }
  .cover-art {
    position: absolute;
    inset: 0;
  }
  .subtitle {
    position: absolute;
    top: 58px;
    left: 0;
    right: 0;
    text-align: center;
    font-family: "Arimo", Arial, sans-serif;
    text-transform: uppercase;
    color: var(--ink-light);
    font-size: 17.5px;
    line-height: 30px;
  }
  .subtitle-lead {
    display: block;
    color: var(--accent);
    font-weight: 700;
    margin-bottom: 5px;
  }
  .title {
    position: absolute;
    left: 0;
    right: 0;
    top: 0;
    margin: 0;
    font-weight: normal;
    color: var(--ink-light);
    text-align: center;
  }
  .title-word {
    position: absolute;
    left: 0;
    right: 0;
    font-family: "Teko", "Arial Narrow", sans-serif;
    font-weight: 500;
    font-size: 212px;
    line-height: 1;
    letter-spacing: 2px;
  }
  .title-joiner {
    position: absolute;
    left: 0;
    right: 0;
    font-family: "Allura", cursive;
    font-size: 108px;
    line-height: 1;
  }
  .w1 { top: 176px; }
  .j1 { top: 360px; }
  .w2 { top: 456px; }
  .w3 { top: 750px; }
  .author {
    position: absolute;
    left: 0;
    right: 0;
    top: 1042px;
    text-align: center;
    font-family: "Arimo", Arial, sans-serif;
    font-weight: 700;
    font-size: 40px;
    letter-spacing: 5px;
    color: var(--ink-light);
  }
</style>
</head>
<body>
  <main class="cover">
    <svg class="cover-art" width="731" height="1128" viewBox="0 0 731 1128" aria-hidden="false">
      <defs>
        <radialGradient id="atmosphere-glow" cx="50%" cy="50%" r="50%">
          <stop offset="0.78" stop-color="#dfeaff" stop-opacity="0.9"/>
          <stop offset="0.86" stop-color="#5a86e0" stop-opacity="0.55"/>
          <stop offset="1" stop-color="#2446b8" stop-opacity="0"/>
        </radialGradient>
        <linearGradient id="earth-fill" x1="0" y1="0" x2="1" y2="1">
          <stop offset="0" stop-color="#3b6bd0"/>
          <stop offset="0.4" stop-color="#b9a07e"/>
          <stop offset="0.6" stop-color="#4d6f4a"/>
          <stop offset="1" stop-color="#1f4fa8"/>
        </linearGradient>
      </defs>
      <ellipse class="atmosphere-band" cx="356" cy="1500" rx="980" ry="960" fill="#3c5cc4" opacity="0.25"/>
      <ellipse class="atmosphere-band" cx="356" cy="1500" rx="860" ry="780" fill="#3a62d0" opacity="0.25"/>
      <circle class="atmosphere-glow" cx="356" cy="1440" r="600" fill="url(#atmosphere-glow)"/>
      <circle class="earth" cx="356" cy="1440" r="495" fill="url(#earth-fill)" role="img" aria-label="Planet Earth seen from orbit, showing desert, green land and ocean"/>
    </svg>

    <p class="subtitle">
      <span class="subtitle-lead">A practical field guide to mending the weather —</span>
      so that the young ones after us inherit steady<br>
      seasons and open skies,
    </p>

    <h1 class="title">
      <span class="title-word w1">WHERE</span>
      <span class="title-joiner j1">the</span>
      <span class="title-word w2">RIVERS</span>
      <span class="title-word w3">MEET</span>
    </h1>

    <p class="author">LORNE WHITCOMBE</p>
  </main>
</body>
</html>
```